Staff Newsletter Template Image

We are looking for two .jpg images that we can put into a Word document and use for our staff newsletter. We will then add content using text boxes.
Attached is the current template which works for the columns and size that we need but we just want a fresh new design.
The Word document shows how we use it.
The name will stay the same - Brightwave Post but can be a different look to the current one.

Target Market(s)

Sales team

Colors

Designer to choose colors to be used in the design.

Requirements
Must have
• Colours will be green, grey and white, possibly cream if needed. All from the guidelines.
• I have attached our brand guidelines which shows design elements and fonts for our brand. Also attached is brand guidelines for one of our product lines as we would like to use the same green.
• It needs to be nice to look at and motivational for our team

```html
<!DOCTYPE html>
<html lang="en">
<head>
<meta charset="utf-8">
<title>Brightwave Post – Staff Newsletter</title>
<link rel="stylesheet" href="https://fonts.googleapis.com/css2?family=Cinzel:wght@500&display=swap">
<style>
  :root {
    --brand-green: #8cc63f;
    --brand-charcoal: #3a3b3b;
    --paper-white: #ffffff;
  }
  html, body {
    margin: 0;
    padding: 0;
    overflow: hidden;
    background: var(--paper-white);
  }
  .newsletter-page {
    position: relative;
    width: 884px;
    height: 1200px;
    background: var(--paper-white);
    overflow: hidden;
  }
  .page-frame {
    position: absolute;
    inset: 0;
    width: 884px;
    height: 1200px;
  }
  .frame-green { fill: var(--brand-green); }
  .frame-charcoal { fill: var(--brand-charcoal); }
  .frame-accent-line {
    fill: none;
    stroke: var(--brand-green);
    stroke-width: 5;
  }
  .masthead-name {
    position: absolute;
    top: 128px;
    left: 548px;
    width: 336px;
    margin: 0;
    text-align: center;
    font-family: "Cinzel", serif;
    font-weight: 500;
    font-size: 24px;
    letter-spacing: 1px;
    color: var(--paper-white);
  }
</style>
</head>
<body>
  <main class="newsletter-page">
    <svg class="page-frame" viewBox="0 0 578 784" preserveAspectRatio="none" aria-hidden="true">
      <!-- top masthead -->
      <path class="frame-charcoal" d="M330 0 H578 V160 H384 Q362 160 354 143 L320 74 H0 V68 H317 Z"/>
      <path class="frame-green" d="M0 0 H340 L354 44 Q358 60 342 60 H0 Z"/>
      <path class="frame-accent-line" d="M313 76 L346 148 Q355 168 382 168 H578"/>
      <!-- footer band -->
      <rect class="frame-green" x="0" y="703" width="578" height="81"/>
      <path class="frame-charcoal" d="M0 703 H288 Q310 703 320 722 L356 784 H0 Z"/>
    </svg>
    <p class="masthead-name">Brightwave Post</p>
  </main>
</body>
</html>
```